Coffee House With Cycling Theme Wants Business Cards

We want to create a business card for a coffee house that has a cycling theme. We expect to use the current logo on one side of the business card and we have been considering adding the words 'COFFEE HOUSE' underneath (see example). For the other side of the business card we want an interesting design with tag-line, address and social media links (the normal business card stuff). See examples provided but we are not fixed on having it exactly as shown, we are very open to great creative ideas. Please note our logo has the initials ‘KR' in orange embedded in the design and this must be retained. However, you can play with the words COFFEE HOUSE as well as use the orange color on the backside of the business card, as you see fit. For an image on the backside of the business card it can be a photo, hand-drawn or whatever but it must visually combine coffee and cycling in some way. The interior of the Coffee House will be reclaimed wood, rustic and have an urban feel to it with cycling artifacts hanging from the walls/ceiling, etc. Finally, it would be beneficial if the business card design elements can be easily used on flyers and other promotional assets. Good luck, we are looking forward to seeing your creative ideas.

Target Market(s)

Coffee lovers and cycling fans

Contact Information for Business Card

See project description.

Colors

Designer to choose colors to be used in the design.

Requirements
Must have
• Must use the current logo provided and combine a coffee and bike theme.
Nice to have
• Orange is used in current logo and could be used as an accent color on the backside of the business card.

```html
<!DOCTYPE html>
<html lang="en">
<head>
<meta charset="utf-8">
<title>KR Coffee House – Business Card</title>
<link rel="stylesheet" href="https://fonts.googleapis.com/css2?family=Open+Sans:wght@400;600&display=swap">
<style>
  :root {
    --stage: #4a4a4a;
    --card-white: #ffffff;
    --card-fade: #e9e9e9;
    --charcoal: #333333;
    --ink: #2a2a2a;
    --orange: #e8601c;
    --muted: #555555;
  }
  * { box-sizing: border-box; margin: 0; padding: 0; }
  html, body { width: 1200px; height: 900px; overflow: hidden; }
  body {
    background: var(--stage);
    font-family: "Open Sans", sans-serif;
    position: relative;
  }
  .card {
    position: absolute;
    left: 290px;
    width: 620px;
    height: 354px;
    border-radius: 18px;
    overflow: hidden;
  }
  .card-front {
    top: 76px;
    background: linear-gradient(160deg, var(--card-fade) 0%, var(--card-white) 45%, var(--card-white) 80%, var(--card-fade) 100%);
  }
  .card-back {
    top: 468px;
    background: var(--charcoal);
    display: flex;
    align-items: center;
    justify-content: center;
  }
  .brand {
    position: absolute;
    left: 40px;
    top: 38px;
    display: flex;
    align-items: center;
    gap: 12px;
  }
  .brand-dot {
    width: 16px; height: 16px;
    border-radius: 50%;
    background: var(--orange);
  }
  .brand-name {
    font-weight: 600;
    font-size: 30px;
    letter-spacing: 2px;
    color: var(--ink);
    line-height: 1;
  }
  .divider {
    position: absolute;
    left: 40px;
    right: 40px;
    top: 128px;
    height: 2px;
    background: var(--orange);
  }
  .contact {
    position: absolute;
    left: 40px;
    top: 148px;
    list-style: none;
    font-size: 15px;
    color: var(--ink);
    line-height: 24px;
  }
  .contact li { display: flex; align-items: center; gap: 8px; }
  .contact svg { width: 12px; height: 12px; flex: none; }
  .person {
    position: absolute;
    right: 40px;
    top: 140px;
    text-align: right;
  }
  .person-name {
    font-size: 24px;
    font-weight: 600;
    letter-spacing: 1.5px;
    color: var(--orange);
    text-transform: uppercase;
  }
  .person-role { font-size: 14px; color: var(--ink); margin-top: 2px; }
  .address {
    position: absolute;
    right: 40px;
    top: 218px;
    text-align: right;
    font-size: 15px;
    line-height: 22px;
    color: var(--ink);
  }
  .social-band {
    position: absolute;
    left: 0; right: 0; bottom: 0;
    height: 50px;
    background: var(--charcoal);
    border-top: 3px solid var(--orange);
    display: flex;
    align-items: center;
    gap: 40px;
    padding-left: 40px;
  }
  .social-item {
    display: flex; align-items: center; gap: 10px;
    color: var(--card-white);
    font-size: 15px;
  }
  .social-mark {
    width: 16px; height: 16px;
    background: var(--orange);
    border-radius: 3px;
  }
  .back-brand {
    display: flex; align-items: center; gap: 18px;
  }
  .back-brand .brand-dot { width: 28px; height: 28px; }
  .back-brand .brand-name {
    font-size: 52px;
    color: var(--orange);
    letter-spacing: 4px;
  }
</style>
</head>
<body>
  <section class="card card-front">
    <div class="brand">
      <span class="brand-dot"></span>
      <span class="brand-name">KR COFFEE HOUSE</span>
    </div>
    <div class="divider"></div>
    <ul class="contact">
      <li>
        <svg viewBox="0 0 12 12"><path d="M3 1l2 2-1 1.5a6 6 0 0 0 3.5 3.5L9 7l2 2-1.5 2C5 11 1 7 1 2.5z" fill="var(--orange)"/></svg>
        (555) 014-2290
      </li>
      <li>
        <svg viewBox="0 0 12 12"><rect x="1" y="2.5" width="10" height="7" fill="none" stroke="var(--orange)" stroke-width="1.2"/><path d="M1 2.5l5 4 5-4" fill="none" stroke="var(--orange)" stroke-width="1.2"/></svg>
        info@krcoffeehouse.com
      </li>
      <li>
        <svg viewBox="0 0 12 12"><circle cx="6" cy="6" r="5" fill="none" stroke="var(--orange)" stroke-width="1.2"/><path d="M1 6h10M6 1c-2.5 3-2.5 7 0 10M6 1c2.5 3 2.5 7 0 10" fill="none" stroke="var(--orange)" stroke-width="1"/></svg>
        www.krcoffeehouse.com
      </li>
    </ul>
    <div class="person">
      <p class="person-name">Daniel Reyes</p>
      <p class="person-role">Director</p>
    </div>
    <address class="address" style="font-style:normal">
      48b Mill Lane,<br>Riverton, NZ, 9010
    </address>
    <div class="social-band">
      <span class="social-item"><span class="social-mark"></span>krcoffeehouse.com</span>
      <span class="social-item"><span class="social-mark"></span>krcoffeehouse.com</span>
    </div>
  </section>

  <section class="card card-back">
    <div class="back-brand">
      <span class="brand-dot"></span>
      <span class="brand-name">KR COFFEE HOUSE</span>
    </div>
  </section>
</body>
</html>
```